Kentucky residential recovery center needs a flyer design

We need a flyer design for a 16 bed male residential/inpatient recovery center based in Fenwick Hollow, Kentucky. The facility provides short term (average 30 day) treatment to those struggling with substace abuse and addiction. The design should communicate trust, assurance, safety.
Our wesite provides more information https://corvalmend.org/treatment-services/residential-treatment/

Target Market(s)

Men (typically 30-50) struggling with substance addiction

```html
<!DOCTYPE html>
<html lang="en">
<head>
<meta charset="utf-8">
<title>Corval Mend – Residential Treatment Flyer</title>
<link rel="stylesheet" href="https://fonts.googleapis.com/css2?family=Montserrat:wght@500;600;700;800;900&family=Poppins:wght@400;500;600&display=swap">
<style>
:root{
  --navy:#2b2b8c;
  --navy-deep:#1f1f6e;
  --indigo:#3a3aa6;
  --green:#2e9c3e;
  --green-bright:#5cc04a;
  --white:#ffffff;
  --ink:#1d1d3a;
  --bg:#eeeeee;
  --photo-warm:#b39b80;
  --photo-wall:#d8cfc3;
}
*{box-sizing:border-box;margin:0;padding:0}
html,body{width:1200px;height:1200px;overflow:hidden;background:var(--bg)}
body{font-family:"Montserrat",sans-serif;color:var(--ink)}
.flyer{position:absolute;left:150px;top:25px;width:900px;height:1150px;background:var(--white);overflow:hidden;box-shadow:0 6px 24px rgba(0,0,0,.18)}
.flyer-art{position:absolute;inset:0}
.abs{position:absolute}
.logo{left:318px;top:50px;width:200px;height:200px;border-radius:50%;background:var(--white);border:5px solid var(--green);display:flex;flex-direction:column;align-items:center;justify-content:center;gap:10px}
.logo-dot{width:24px;height:24px;border-radius:50%;background:var(--navy)}
.logo-name{font-weight:800;font-size:20px;color:var(--navy);letter-spacing:1px}
.headline{right:65px;top:112px;text-align:right;font-weight:900;font-size:42px;line-height:1.05;color:var(--green-bright);text-transform:uppercase}
.subhead{right:65px;top:226px;text-align:right;font-weight:700;font-size:25px;line-height:1.15;color:var(--white)}
.subhead-rule{right:65px;top:293px;width:140px;height:2px;background:var(--green-bright)}
.intro{right:65px;top:312px;text-align:right;font-weight:500;font-size:17px;line-height:1.4;color:var(--white);white-space:nowrap}
.ribbon{background:var(--green);color:var(--white);font-weight:800;text-transform:uppercase;text-align:center;border-radius:14px;box-shadow:0 4px 8px rgba(0,0,0,.25)}
.ribbon--issues{left:515px;top:395px;width:275px;height:70px;font-size:20px;line-height:1.3;padding-top:8px}
.issues{left:390px;top:505px;width:480px;display:flex;justify-content:space-between;list-style:none}
.issue{width:120px;text-align:center;font-family:"Poppins",sans-serif;font-size:13.5px;line-height:1.3;color:var(--ink)}
.issue-icon{width:78px;height:78px;margin:0 auto 10px;border-radius:50%;background:var(--navy);border:3px solid var(--green);display:flex;align-items:center;justify-content:center}
.why{left:55px;top:625px;width:290px;height:425px;border-radius:28px;background:linear-gradient(180deg,var(--navy-deep),var(--indigo));color:var(--white);text-align:center;padding-top:62px;box-shadow:0 6px 12px rgba(0,0,0,.25)}
.why-tab{left:90px;top:608px;width:220px;height:62px;background:var(--green);color:var(--white);border-radius:0 0 18px 18px;font-weight:800;font-size:20px;line-height:1.1;text-align:center;padding-top:9px;text-transform:uppercase}
.stat{padding:12px 0;border-bottom:1px solid rgba(255,255,255,.25);margin:0 18px}
.stat:last-child{border-bottom:0}
.stat-value{font-weight:900;font-size:40px;line-height:1}
.stat-label{font-weight:600;font-size:13px;letter-spacing:.5px;text-transform:uppercase;margin-top:6px;white-space:nowrap}
.stat-label--small{font-size:10.5px;letter-spacing:.2px}
.ribbon--process{left:480px;top:655px;width:420px;height:68px;border-radius:34px 0 0 34px;text-align:left;padding:9px 0 0 40px}
.ribbon-kicker{font-size:10.5px;font-weight:700;display:block;padding-left:45px}
.ribbon-title{font-size:27px;font-weight:900}
.stage{right:65px;width:400px;display:flex;align-items:flex-start;gap:16px;justify-content:flex-end}
.stage-text{text-align:right;font-family:"Poppins",sans-serif;font-size:14.5px;line-height:1.3;color:var(--ink)}
.stage-label{display:inline-block;font-family:"Montserrat",sans-serif;font-weight:800;font-size:15px;color:var(--navy);border-right:2px solid var(--green);border-radius:0 10px 10px 0;padding-right:6px;margin-bottom:4px}
.stage-icon{flex:none;width:66px;height:66px;border-radius:50%;background:var(--navy);border:3px solid var(--green);display:flex;align-items:center;justify-content:center}
.footer{left:0;top:1075px;width:900px;height:58px;background:var(--green);color:var(--white);display:flex;align-items:center;padding:0 36px;gap:24px}
.footer-phone{font-weight:800;font-size:30px;display:flex;align-items:center;gap:8px;white-space:nowrap}
.footer-web,.footer-address{font-weight:600;font-size:13px;line-height:1.45;white-space:nowrap}
</style>
</head>
<body>
<main class="flyer">
  <svg class="flyer-art" width="900" height="1150" viewBox="0 0 900 1150">
    <defs>
      <linearGradient id="panelGrad" x1="0" y1="0" x2="1" y2="1">
        <stop offset="0" stop-color="#22227a"/>
        <stop offset="1" stop-color="#3434a0"/>
      </linearGradient>
      <clipPath id="roomClip">
        <path d="M0 20 H420 C450 120 470 250 430 380 C400 480 340 540 260 570 L0 620 Z"/>
      </clipPath>
    </defs>
    <path d="M330 0 H900 V470 C820 430 700 410 560 420 C480 425 420 440 370 460 Z" fill="url(#panelGrad)"/>
    <path d="M380 0 C450 70 560 90 700 80 C790 74 850 60 900 45 V0 Z" fill="var(--green)"/>
    <path d="M430 0 C520 60 640 80 760 70 C830 64 870 55 900 50 V0 Z" fill="var(--white)"/>
    <path d="M560 420 C700 410 820 430 900 470 V488 C820 450 700 432 560 440 Z" fill="var(--green)"/>
    <g clip-path="url(#roomClip)">
      <rect x="0" y="0" width="480" height="640" fill="var(--photo-wall)" role="img" aria-label="Photo of a residential bedroom with bunk beds and wood floor"/>
      <rect x="0" y="330" width="480" height="310" fill="var(--photo-warm)"/>
    </g>
    <path d="M420 20 C450 120 470 250 430 380 C400 480 340 540 260 570" fill="none" stroke="var(--green)" stroke-width="5"/>
    <circle cx="105" cy="520" r="102" fill="#8a7460" stroke="var(--green)" stroke-width="5" role="img" aria-label="Photo of a lounge with leather sofa and desk"/>
    <circle cx="305" cy="470" r="82" fill="#9d958c" stroke="var(--green)" stroke-width="5" role="img" aria-label="Photo of a meeting room with a round table and chairs"/>
  </svg>

  <div class="abs logo"><span class="logo-dot"></span><span class="logo-name">CORVAL MEND</span></div>

  <h1 class="abs headline">Spaces<br>Available!</h1>
  <h2 class="abs subhead">Residential / Inpatient<br>Treatment</h2>
  <div class="abs subhead-rule"></div>
  <p class="abs intro">16 bed male residential/inpatient<br>recovery center based in Fenwick Hollow,</p>

  <div class="abs ribbon ribbon--issues">What issues<br>can be treated?</div>

  <ul class="abs issues">
    <li class="issue"><div class="issue-icon"><svg width="34" height="44" viewBox="0 0 34 44"><path d="M13 2h8v10l5 6v24H8V18l5-6z" fill="var(--white)"/><rect x="12" y="24" width="10" height="12" fill="var(--navy)"/></svg></div>ALCOHOLISM</li>
    <li class="issue"><div class="issue-icon"><svg width="44" height="44" viewBox="0 0 44 44"><rect x="18" y="4" width="8" height="28" rx="2" fill="var(--white)" transform="rotate(45 22 22)"/><circle cx="31" cy="32" r="7" fill="var(--white)"/><circle cx="12" cy="32" r="6" fill="var(--white)"/></svg></div>DRUG<br>ADDICTION</li>
    <li class="issue"><div class="issue-icon"><svg width="36" height="44" viewBox="0 0 36 44"><rect x="8" y="2" width="20" height="7" rx="2" fill="var(--white)"/><rect x="4" y="11" width="28" height="31" rx="5" fill="var(--white)"/><path d="M15 20h6v6h6v6h-6v6h-6v-6H9v-6h6z" fill="var(--navy)"/></svg></div>MEDICATION<br>ADDICTION</li>
    <li class="issue"><div class="issue-icon"><svg width="44" height="44" viewBox="0 0 44 44"><path d="M20 4c10 0 17 7 17 16l4 8h-5v8h-8v6H12V32C6 28 3 22 4 16 6 9 12 4 20 4z" fill="var(--white)"/><path d="M8 20h7l3-6 4 12 3-6h8" fill="none" stroke="var(--navy)" stroke-width="2.5"/></svg></div>BEHAVIORAL<br>HEALTH</li>
  </ul>

  <section class="abs why">
    <div class="stat"><div class="stat-value">100+</div><div class="stat-label">Years</div></div>
    <div class="stat"><div class="stat-value">95%</div><div class="stat-label">Satisfaction rating</div></div>
    <div class="stat"><div class="stat-value">#1</div><div class="stat-label stat-label--small">Best drug &amp; alcohol rehab center</div></div>
    <div class="stat"><div class="stat-value">2,500+</div><div class="stat-label">Patients treated</div></div>
  </section>
  <div class="abs why-tab">Why<br>choose us?</div>

  <div class="abs ribbon ribbon--process"><span class="ribbon-kicker">Stages of residential recovery process</span><span class="ribbon-title">HOW DOES IT WORK?</span></div>

  <div class="abs stage" style="top:748px">
    <p class="stage-text"><span class="stage-label">STAGE 1</span><br>Speak with our team in private about<br>the nature of your challenges and<br>what you need help with</p>
    <div class="stage-icon"><svg width="36" height="32" viewBox="0 0 36 32"><path d="M3 3h20v14H10l-5 5v-5H3z" fill="var(--white)"/><path d="M26 9h7v14h-2v5l-5-5H13v-3h13z" fill="var(--white)"/></svg></div>
  </div>
  <div class="abs stage" style="top:850px">
    <p class="stage-text"><span class="stage-label">STAGE 2</span><br>Together we select an appropriate time<br>slot to book you in for an induction<br>appointment with one of our clinical staff</p>
    <div class="stage-icon"><svg width="34" height="36" viewBox="0 0 34 36"><circle cx="17" cy="10" r="7" fill="var(--white)"/><path d="M3 34c0-9 6-14 14-14s14 5 14 14z" fill="var(--white)"/></svg></div>
  </div>
  <div class="abs stage" style="top:955px">
    <p class="stage-text"><span class="stage-label">STAGE 3</span><br>Once the induction is completed, we'll<br>schedule you in to commence your<br>inpatient program</p>
    <div class="stage-icon"><svg width="28" height="30" viewBox="0 0 28 30"><path d="M4 2l22 13L4 28z" fill="var(--white)"/></svg></div>
  </div>

  <footer class="abs footer">
    <div class="footer-phone"><svg width="16" height="28" viewBox="0 0 16 28"><rect x="1" y="1" width="14" height="26" rx="3" fill="none" stroke="var(--white)" stroke-width="2"/></svg>555 010-0142</div>
    <div class="footer-web">⊕ www.corvalmend.org<br>✉ admissions@corvalmend.com</div>
    <div class="footer-address"><svg width="10" height="13" viewBox="0 0 10 13"><path d="M5 0a5 5 0 0 1 5 5c0 3-5 8-5 8S0 8 0 5a5 5 0 0 1 5-5z" fill="var(--white)"/></svg> 2480 Harlow Ridge Drive, Fenwick Hollow,<br>Westmark 60123</div>
  </footer>
</main>
</body>
</html>
```